Flyer Design Print Ad for Clothing Store

We are a modest women's clothing store. We are looking for a print ad 90*134 mm that is attention grabbing and can serve as a template for us going forward. We cannot use pictures of actual women. We need it to include our logo, store hours, physical address, www.linenhour.example, 050-000-0000. We would use this template and change the call to action as necessary e. g. BOGO Sale, 30% off, flash sale, summer sale etc. Our colors are black and white and our fonts are Bodoni sans and Athens.

Target Market(s)

Women from teen to age 70

Industry/Entity Type

Women's clothing

Font styles to use
Other font styles liked:
• Athens, Bodoni Sans

Requirements
Must have
• Our, logo, 050-000-0000, www.linenhour.example, address and store hours
Nice to have
• I'd like something that's not just our flat logo but something that will make someone pause to look
Should not have
• Pictures of women

```html
<!DOCTYPE html>
<html lang="en">
<head>
<meta charset="utf-8">
<title>Linenhour – BOGO Sale Flyer</title>
<link rel="stylesheet" href="https://fonts.googleapis.com/css2?family=Marcellus&family=Open+Sans:wght@400;600;700&display=swap">
<style>
  :root {
    --ink: #1d1d1d;
    --paper: #ffffff;
    --backdrop: #ebebeb;
    --silver-dark: #7f8282;
    --silver-light: #f4f6f6;
    --floral-mid: #9a9a9a;
    --floral-light: #cfcfcf;
  }
  * { margin: 0; padding: 0; box-sizing: border-box; }
  html, body { width: 1200px; height: 1200px; overflow: hidden; background: var(--backdrop); }
  .stage { position: relative; width: 1200px; height: 1200px; }
  .flyer {
    position: absolute; left: 251.5px; top: 80.7px;
    width: 1122px; height: 1672px;
    transform: scale(0.6211); transform-origin: 0 0;
    background: var(--paper); overflow: hidden;
    font-family: "Marcellus", serif; color: var(--ink);
  }
  .flyer > * { position: absolute; }
  .backdrop-shape { left: 0; top: 0; width: 1122px; height: 1672px; }
  .floral--top {
    right: 0; top: 0; width: 330px; height: 400px;
    background: radial-gradient(ellipse 60% 55% at 72% 28%, var(--floral-light) 0%, rgba(154,154,154,0.7) 45%, rgba(29,29,29,0) 100%);
  }
  .floral--bottom {
    left: 0; top: 1195px; width: 430px; height: 477px;
    background: radial-gradient(ellipse 70% 65% at 28% 78%, #7a7a7a 0%, rgba(154,154,154,0.75) 45%, rgba(255,255,255,0) 100%);
  }
  .frame { left: 0; top: 0; width: 1122px; height: 1672px; mix-blend-mode: difference; pointer-events: none; }
  .line { left: 0; width: 1122px; text-align: center; line-height: 1; white-space: nowrap; }
  .brand-mark { left: 499px; top: 88px; width: 124px; height: 124px; border-radius: 50%; background: var(--paper); }
  .brand-name { top: 238px; font-size: 30px; letter-spacing: 9px; color: var(--paper); }
  .silver {
    background: linear-gradient(100deg, var(--silver-dark) 0%, var(--silver-light) 22%, #a9acac 40%, var(--silver-light) 60%, #8d9090 80%, var(--silver-light) 100%);
    -webkit-background-clip: text; background-clip: text; color: transparent;
  }
  .headline-top { top: 290px; font-size: 172px; font-weight: 400; }
  .headline-main { top: 432px; font-size: 318px; letter-spacing: -4px; }
  .divider { left: 138px; top: 742px; width: 873px; height: 1px; background: var(--paper); }
  .divider-mark { left: 551px; top: 732px; width: 20px; height: 20px; background: var(--paper); transform: rotate(45deg); }
  .offer { top: 776px; font-size: 150px; color: var(--paper); }
  .icon-badge { display: block; }
  .pin-badge { left: 509px; top: 957px; width: 106px; height: 106px; }
  .calendar-badge { left: 509px; top: 1340px; width: 104px; height: 104px; }
  .place-he { top: 1080px; font-family: "Open Sans", sans-serif; font-weight: 700; font-size: 46px; direction: rtl; }
  .place-en { top: 1138px; font-size: 35px; }
  .place-note { top: 1185px; font-family: "Open Sans", sans-serif; font-size: 26px; direction: rtl; }
  .place-alt { top: 1226px; font-family: "Open Sans", sans-serif; font-size: 22px; direction: rtl; }
  .buses { top: 1265px; font-size: 38px; }
  .hours { font-family: "Open Sans", sans-serif; font-weight: 700; font-size: 38px; }
  .hours--days { top: 1460px; }
  .hours--evening { top: 1514px; }
  .contact { top: 1568px; font-family: "Open Sans", sans-serif; font-weight: 600; font-size: 24px; }
  .base-band { left: 395px; top: 1615px; width: 727px; height: 57px; background: var(--ink); }
</style>
</head>
<body>
<div class="stage">
  <section class="flyer">
    <svg class="backdrop-shape" viewBox="0 0 1122 1672" aria-hidden="true">
      <rect x="0" y="0" width="1122" height="171" fill="var(--ink)"/>
      <ellipse cx="561" cy="171" rx="800" ry="854" fill="var(--ink)"/>
    </svg>
    <div class="base-band"></div>
    <div class="floral--top" role="img" aria-label="Grey watercolour leaves and flowers in the top corner"></div>
    <div class="floral--bottom" role="img" aria-label="Grey watercolour flower bouquet in the bottom corner"></div>
    <svg class="frame" viewBox="0 0 1122 1672" aria-hidden="true">
      <rect x="59" y="55" width="1006" height="1558" fill="none" stroke="#ffffff" stroke-width="5"/>
    </svg>

    <div class="brand-mark"></div>
    <p class="line brand-name">LINENHOUR</p>

    <h1 class="line headline-top silver">BOGO</h1>
    <p class="line headline-main silver">SALE</p>
    <div class="divider"></div>
    <div class="divider-mark"></div>
    <p class="line offer">30% OFF</p>

    <svg class="icon-badge pin-badge" viewBox="0 0 106 106" aria-hidden="true">
      <circle cx="53" cy="53" r="51" fill="var(--paper)" stroke="var(--ink)" stroke-width="3"/>
      <path d="M53 28c-11 0-19 8-19 18 0 13 19 33 19 33s19-20 19-33c0-10-8-18-19-18z" fill="var(--ink)"/>
      <circle cx="53" cy="46" r="7" fill="var(--paper)"/>
    </svg>

    <p class="line place-he">מרכז מסחרי גבעת הארזים</p>
    <p class="line place-en">CEDAR HILL SHOPPING CENTER</p>
    <p class="line place-note">(מעל קפה לימון)</p>
    <p class="line place-alt">ניתן להגיע גם מרחוב הארזים 16</p>
    <p class="line buses">Buses 21, 22, 39, 41, 45, 52, 59, 65, 68, 69, 77</p>

    <svg class="icon-badge calendar-badge" viewBox="0 0 104 104" aria-hidden="true">
      <circle cx="52" cy="52" r="52" fill="var(--ink)"/>
      <rect x="28" y="32" width="40" height="38" rx="3" fill="var(--paper)"/>
      <rect x="28" y="32" width="40" height="9" fill="#cfcfcf"/>
      <rect x="34" y="26" width="4" height="10" fill="var(--paper)"/>
      <rect x="58" y="26" width="4" height="10" fill="var(--paper)"/>
      <g fill="var(--ink)">
        <rect x="33" y="46" width="6" height="5"/><rect x="42" y="46" width="6" height="5"/><rect x="51" y="46" width="6" height="5"/>
        <rect x="33" y="55" width="6" height="5"/><rect x="42" y="55" width="6" height="5"/>
      </g>
      <circle cx="66" cy="66" r="13" fill="var(--paper)" stroke="var(--ink)" stroke-width="3"/>
      <path d="M66 59v8h6" fill="none" stroke="var(--ink)" stroke-width="3"/>
    </svg>

    <p class="line hours hours--days">S-Th- 10:30-12:30 <span dir="rtl">א-ה-</span></p>
    <p class="line hours hours--evening">20:30 - 22:30</p>
    <p class="line contact">050-000-0000 &nbsp;|&nbsp; www.linenhour.example</p>
  </section>
</div>
</body>
</html>
```